Mortgage Protection Insurance Flyer

The target audience are new home owners so the design needs to be clean and simple.

This a primarily for Final Expense Insurance, but need an area where it says "We Also Specialize In:"
- Medicare Supplement Insurance (MediGap)
- Annuities
- Final Expense

All flyer versions need to be editable. Colors to be used are red, white or black. Refer to my website for colors and photos (corvantshield.com). Will attach my logo and a flyer that I found online that is the format that I am looking for (for 8.5 in. x 11 in version). Need flyer in standard letter size 8.5 in. x11 in. but also in 8.5 in. x 5.5 in and 5.0 in. x 8.0 in. All sizes to be portrait oriented. If picked as winning design, need all flyer versions in full color, also in grey scale and files in all industry file types.

Content can be taken from my website..... corvantshield.com

Do NOT submit if you are not willing to provide all versions as described above for the original project price.

Must use royalty-free stock photos please.

Target Market(s)

New homeowners looking for insurance to protect there mortgage payments

Industry/Entity Type

Life Insurance

Colors
f69fa3

Requirements
Must have
• Colors to be used are red, white or black.
• Need flyer in standard letter size 8.5 in. x11 in. but also in 3.5 in. x 8.5 in (Full Bleed 3.75 in by 8.75 in.) and 4.0 in. x 6.0 in. (Full Bleed 4.12 in x 6.12 in) Each design tailored to the size dimensions (So no squeezing 8.5 x 11 design into a 4.0 x 6.0 space.) All sizes to be portrait oriented. If picked as winning design, need all flyer versions in full color, also in grey scale and files in all file types.
• Do not need physical address on flyer, do need email address on flyer though - tkelwer@corvantshield.com
• So phone number should be prominent, email address and website address should also be contact area.
• If you can not agree to terms above, do not submit any designs.
• Need facebook & twitter logos somewhere in contact info area.
Nice to have
• See sample flyers I have attached.
• White background with red used as primary graphic color and black used as secondary graphic if needed.
• font to be used should similar to one used in logo.

```html
<!DOCTYPE html>
<html lang="en">
<head>
<meta charset="utf-8">
<title>Corvant Shield Flyer Set</title>
<link href="https://fonts.googleapis.com/css2?family=Oswald:wght@500;700&family=Roboto:wght@400;500;700;900&display=swap" rel="stylesheet">
<style>
:root{
  --bg-left:#f6b1b1;
  --bg-right:#f29494;
  --red:#e60000;
  --red-dark:#9e0e12;
  --ink:#1d1d1d;
  --grey:#d4d4d4;
  --paper:#ffffff;
}
*{margin:0;padding:0;box-sizing:border-box}
html,body{width:1200px;height:1200px;overflow:hidden}
body{position:relative;font-family:"Roboto",sans-serif;color:var(--ink);
  background:linear-gradient(90deg,var(--bg-left) 0 643px,var(--bg-right) 643px 100%)}
.sheet{position:absolute;background:var(--paper);overflow:hidden}
.abs{position:absolute}
.brand{position:absolute;display:flex;align-items:center;gap:5px;font-family:"Roboto",sans-serif;font-weight:900;color:var(--ink);letter-spacing:.3px;white-space:nowrap;line-height:1}
.brand .mark{width:.7em;height:.7em;background:var(--red)}
.headline{position:absolute;font-family:"Oswald",sans-serif;font-weight:700;line-height:1;text-transform:uppercase}
.headline .red{color:var(--red)}
.headline .sub{font-weight:500}
.section-title{position:absolute;color:var(--red);font-weight:700}
.body-copy{position:absolute;color:#333;line-height:1.3}
.benefits{position:absolute;background:linear-gradient(180deg,#ff0000,#b20d10);border-radius:10px;color:#fff}
.benefits .tab{position:absolute;left:-8px;background:#333;color:#fff;font-weight:700;border-radius:0 8px 8px 0}
.benefits ul{list-style:none;position:absolute}
.benefits li{position:relative;font-weight:500;line-height:1.25}
.benefits li::before,.tick-list li::before{content:"";position:absolute;left:0;top:.1em;width:.85em;height:.85em;border:1px solid currentColor;border-radius:50%}
.tick-list{list-style:none;position:absolute}
.tick-list li{position:absolute;white-space:nowrap;color:#333}
.tick-list li::before{border-color:var(--red)}
.contact-row{position:absolute;display:flex;align-items:center;gap:5px;color:#fff;font-weight:700;white-space:nowrap}
.contact-row .ring{border:1.2px solid #fff;border-radius:50%;display:flex;align-items:center;justify-content:center}
.social{position:absolute;display:flex;gap:2px}
.social span{background:#fff;border-radius:1px}
</style>
</head>
<body>

<!-- Postcard front -->
<section class="sheet" style="left:73px;top:207px;width:500px;height:333px">
  <svg class="abs" width="500" height="333" viewBox="0 0 500 333">
    <defs>
      <linearGradient id="pcPhoto" x1="0" y1="0" x2="1" y2="1">
        <stop offset="0" stop-color="#f4f6f8"/><stop offset=".6" stop-color="#dfe3e6"/><stop offset="1" stop-color="#c9cfd3"/>
      </linearGradient>
    </defs>
    <path role="img" aria-label="Photo of a smiling senior couple embracing at home" fill="url(#pcPhoto)" d="M0 0H500V200C430 175 330 190 230 210C150 225 60 235 0 235Z"/>
    <path fill="#fff" d="M0 0H215C185 48 115 80 0 82Z"/>
    <path fill="none" stroke="#1d1d1d" stroke-width="4" d="M0 80C115 80 185 48 215 0"/>
    <path fill="none" stroke="#e60000" stroke-width="3" d="M215 0C208 12 200 20 192 27"/>
    <path fill="#fff" d="M0 235C60 235 150 225 230 210C330 190 430 175 500 200V333H0Z"/>
    <path fill="none" stroke="#1d1d1d" stroke-width="4" d="M0 188C120 205 250 185 330 180C410 175 460 190 500 210"/>
    <path fill="none" stroke="#e60000" stroke-width="3" d="M0 202C140 212 260 195 340 188C420 182 470 200 500 230"/>
    <rect x="0" y="324" width="500" height="3" fill="#1d1d1d"/>
    <rect x="0" y="329" width="500" height="4" fill="#e60000"/>
  </svg>
  <div class="brand" style="left:31px;top:39px;font-size:11px"><span class="mark"></span>CORVANT SHIELD</div>
  <div class="headline" style="left:28px;top:92px;font-size:29px">Our</div>
  <div class="headline" style="left:28px;top:124px;font-size:29px"><span class="red">Plans Are</span></div>
  <div class="headline" style="left:28px;top:157px;font-size:18px"><span class="sub">Based on Yours</span></div>
  <div class="section-title" style="left:28px;top:223px;font-size:7.5px">Final Expense Insurance</div>
  <div class="body-copy" style="left:28px;top:239px;width:236px;font-size:6.2px;text-align:justify">Final Expense Insurance is a type of permanent life insurance where the death benefit is used to cover (but not limited to) medical costs, funeral costs and other end-of-life expenses. It is a budget friendly option with a death benefit of up to $40k.</div>
  <div class="abs" style="left:28px;top:279px;width:104px;height:11px;background:var(--grey);font-size:6.5px;font-weight:500;padding:2px 4px">Monthly premiums as low as</div>
  <div class="abs" style="left:134px;top:279px;width:46px;height:11px;background:var(--red);color:#fff;font-size:6.5px;font-weight:700;text-align:center;padding-top:2px">$11*</div>
  <div class="abs" style="left:28px;top:295px;width:104px;height:11px;background:var(--grey);font-size:6.5px;font-weight:500;padding:2px 4px">Death Benefits as high as</div>
  <div class="abs" style="left:134px;top:295px;width:46px;height:11px;background:var(--red);color:#fff;font-size:6.5px;font-weight:700;text-align:center;padding-top:2px">$40,000</div>
  <div class="benefits" style="left:294px;top:138px;width:150px;height:170px">
    <div class="tab" style="top:14px;width:58px;height:12px;font-size:6.5px;padding:2px 0 0 12px">Benefits:</div>
    <ul style="left:10px;top:32px;width:134px;font-size:5.4px">
      <li style="padding-left:9px;margin-bottom:7px">All plans we offer are state regulated</li>
      <li style="padding-left:9px;margin-bottom:7px">Relatively low monthly premiums</li>
      <li style="padding-left:9px;margin-bottom:7px">Premiums can never increase</li>
      <li style="padding-left:9px;margin-bottom:7px">Your policy can never be cancelled as long as you pay your premium</li>
      <li style="padding-left:9px;margin-bottom:7px">No medical exams</li>
      <li style="padding-left:9px;margin-bottom:7px">Guaranteed Death Benefit</li>
      <li style="padding-left:9px">Many policies we offer are Guaranteed Acceptance, "Day 1" coverage, have a child/grandchild rider and/or have an accelerated death benefit rider</li>
    </ul>
  </div>
</section>

<!-- Postcard back -->
<section class="sheet" style="left:73px;top:646px;width:500px;height:333px">
  <div class="abs" style="left:0;top:0;width:283px;height:333px;box-shadow:3px 0 6px rgba(0,0,0,.18);background:#fff">
    <div class="brand" style="left:28px;top:41px;font-size:11px"><span class="mark"></span>CORVANT SHIELD</div>
    <div class="abs" style="left:155px;top:32px;width:1.5px;height:30px;background:var(--red)"></div>
    <div class="body-copy" style="left:168px;top:36px;font-size:8px;line-height:1.35">PO Box 412<br>Alder Falls, ID 83000</div>
    <div class="body-copy" style="left:23px;top:84px;width:255px;font-size:6.2px">We have been helping clients in Northern Idaho/Eastern Washington prepare for the unknown.</div>
    <div class="body-copy" style="left:23px;top:109px;width:255px;font-size:6.2px">We have access to the industry's top insurance carriers so you can get the right coverage, that fits your budget.</div>
    <div class="body-copy" style="left:23px;top:134px;width:255px;font-size:6.2px">Find out how we can give you the peace of mind knowing your family wont have a financial burden if something were to happen to you.</div>
    <div class="section-title" style="left:24px;top:161px;font-size:7.5px">We Also Specialize In:</div>
    <ul class="tick-list" style="left:24px;top:176px;font-size:6.3px">
      <li style="left:0;top:0;padding-left:10px">Medicare Supplement Insurance (Medigap)</li>
      <li style="left:168px;top:0;padding-left:10px">Annuities</li>
      <li style="left:0;top:18px;padding-left:10px">Mortgage Protection Insurance</li>
    </ul>
    <div class="body-copy" style="left:105px;top:220px;width:170px;font-size:4.8px">*Based on an insured that is a 65 year old, non-smoking female that has no medical conditions with a death benefit of $2k</div>
    <svg class="abs" style="left:0;top:232px" width="283" height="101" viewBox="0 0 283 101">
      <defs><linearGradient id="backBand" x1="0" y1="0" x2="0" y2="1"><stop offset="0" stop-color="#ee1111"/><stop offset="1" stop-color="#9e0e12"/></linearGradient></defs>
      <path fill="url(#backBand)" d="M0 10C90 -2 200 -2 283 18V101H0Z"/>
      <path fill="none" stroke="#1d1d1d" stroke-width="3" d="M0 6C90 -6 200 -6 283 14"/>
    </svg>
    <div class="abs" style="left:25px;top:255px;color:#fff;font-weight:500;font-size:10.5px;line-height:1.25">GUARANTEED<br>APPROVAL!</div>
    <div class="abs" style="left:25px;top:284px;width:86px;height:1px;background:rgba(255,255,255,.7)"></div>
    <div class="abs" style="left:24px;top:290px;color:#fff;font-weight:700;font-size:10px">Call us now:</div>
    <div class="abs" style="left:24px;top:303px;color:#fff;font-weight:700;font-size:15.5px">(555)014.2276</div>
    <div class="contact-row" style="left:140px;top:285px;font-size:6px"><span class="ring" style="width:15px;height:15px"><svg width="8" height="6" viewBox="0 0 8 6"><rect x=".5" y=".5" width="7" height="5" fill="none" stroke="#fff"/><path d="M.5 .5L4 3.5L7.5 .5" fill="none" stroke="#fff"/></svg></span>tkelwer@corvantshield.com</div>
    <div class="contact-row" style="left:140px;top:305px;font-size:6px"><span class="ring" style="width:15px;height:15px"><svg width="9" height="9" viewBox="0 0 10 10"><circle cx="5" cy="5" r="4.2" fill="none" stroke="#fff"/><ellipse cx="5" cy="5" rx="1.8" ry="4.2" fill="none" stroke="#fff"/><path d="M.8 5H9.2" stroke="#fff"/></svg></span>corvantshield.com</div>
    <div class="social" style="left:259px;top:314px"><span style="width:8px;height:8px"></span><span style="width:8px;height:8px"></span></div>
  </div>
</section>

<!-- Letter flyer -->
<section class="sheet" style="left:728px;top:137px;width:377px;height:879px">
  <svg class="abs" width="377" height="879" viewBox="0 0 377 879">
    <defs>
      <linearGradient id="flyPhoto" x1="0" y1="0" x2="1" y2="1">
        <stop offset="0" stop-color="#f5f7f9"/><stop offset=".55" stop-color="#e1e5e8"/><stop offset="1" stop-color="#c8ced2"/>
      </linearGradient>
      <linearGradient id="flyBand" x1="0" y1="0" x2="0" y2="1"><stop offset="0" stop-color="#ee1111"/><stop offset="1" stop-color="#9e0e12"/></linearGradient>
    </defs>
    <path role="img" aria-label="Photo of a smiling senior couple embracing on a sofa" fill="url(#flyPhoto)" d="M0 0H377V290C300 300 200 305 120 300C70 297 30 295 0 300Z"/>
    <path fill="#fff" d="M0 0H258C235 60 135 102 0 105Z"/>
    <path fill="none" stroke="#1d1d1d" stroke-width="4" d="M0 104C135 101 235 60 258 0"/>
    <path fill="none" stroke="#e60000" stroke-width="3" d="M258 0C252 11 244 21 236 29"/>
    <path fill="#fff" d="M0 330C90 318 200 325 280 320C330 317 360 312 377 305V879H0Z"/>
    <path fill="none" stroke="#1d1d1d" stroke-width="5" d="M0 296C80 310 180 318 260 312C320 308 360 298 377 290"/>
    <path fill="none" stroke="#e60000" stroke-width="3.5" d="M0 312C90 326 190 330 270 322C330 316 360 306 377 300"/>
    <path fill="url(#flyBand)" d="M0 775C60 760 140 765 220 762C300 760 350 748 377 725V879H0Z"/>
    <path fill="none" stroke="#1d1d1d" stroke-width="4" d="M0 768C60 752 140 758 220 755C300 752 350 740 377 718"/>
  </svg>
  <div class="brand" style="left:30px;top:45px;font-size:15px"><span class="mark"></span>CORVANT SHIELD</div>
  <div class="headline" style="left:28px;top:164px;font-size:39px">Our</div>
  <div class="headline" style="left:28px;top:206px;font-size:39px"><span class="red">Plans Are</span></div>
  <div class="headline" style="left:28px;top:249px;font-size:23px"><span class="sub">Based on Yours</span></div>
  <div class="section-title" style="left:30px;top:344px;font-size:12.5px;line-height:1.05">Mortgage Protection<br>Insurance</div>
  <div class="body-copy" style="left:30px;top:380px;width:132px;font-size:8.4px;text-align:justify">Mortgage Protection Insurance (MPI) is a type of decreasing term life insurance policy designed to pay off your mortgage if you were to pass away — and many policies also cover mortgage payments (usually for a limited period of time) if you become disabled.</div>
  <div class="body-copy" style="left:30px;top:476px;width:132px;font-size:8.4px;text-align:justify">Unforeseen events and a lack of the right kind of insurance can spell trouble quickly. Contact us today, to set up a free assessment time. We will analyze your insurance needs and get you and your family the right coverage quickly at a budget friendly price.</div>
  <div class="benefits" style="left:186px;top:340px;width:155px;height:206px">
    <div class="tab" style="top:16px;width:76px;height:15px;font-size:8.5px;padding:2px 0 0 18px">Benefits:</div>
    <ul style="left:13px;top:40px;width:136px;font-size:6.6px;font-weight:700">
      <li style="padding-left:12px;margin-bottom:10px">Guaranteed approval. Even if you're in poor health or work in a dangerous profession, there is guaranteed approval with no medical exams or lab tests.</li>
      <li style="padding-left:12px;margin-bottom:10px">No guesswork. The check goes straight to the lender for the exact mortgage balance, so there'll always be enough and your family won't have to handle the money.</li>
      <li style="padding-left:12px">Disability protection. Many MPI policies make mortgage payments (usually for a limited time) if you become disabled or lose your job.</li>
    </ul>
  </div>
  <div class="body-copy" style="left:30px;top:591px;width:320px;font-size:8.6px">We have been helping clients in Northern Idaho/Eastern Washington prepare for the unknown.</div>
  <div class="body-copy" style="left:30px;top:628px;width:320px;font-size:8.6px">We have access to the industry's top insurance carriers so you can get the right coverage, that fits your budget.</div>
  <div class="body-copy" style="left:30px;top:664px;width:320px;font-size:8.6px">Find out how we can give you the peace of mind knowing your family wont have a financial burden if something were to happen to you.</div>
  <div class="section-title" style="left:31px;top:702px;font-size:12px">We Also Specialize In:</div>
  <ul class="tick-list" style="left:31px;top:723px;font-size:8.4px">
    <li style="left:0;top:0;padding-left:14px">Medicare Supplement Insurance (Medigap)</li>
    <li style="left:205px;top:1px;padding-left:22px">Annuities</li>
    <li style="left:0;top:15px;padding-left:14px">Final Expense Insurance</li>
  </ul>
  <div class="abs" style="left:26px;top:801px;color:#fff;font-weight:700;font-size:11.5px">Call us now:</div>
  <div class="abs" style="left:25px;top:817px;color:#fff;font-weight:700;font-size:19px">(555)014.2276</div>
  <div class="contact-row" style="left:175px;top:801px;font-size:7.2px"><span class="ring" style="width:20px;height:20px"><svg width="10" height="8" viewBox="0 0 10 8"><rect x=".5" y=".5" width="9" height="7" fill="none" stroke="#fff"/><path d="M.5 .5L5 4.5L9.5 .5" fill="none" stroke="#fff"/></svg></span>tkelwer@corvantshield.com</div>
  <div class="contact-row" style="left:175px;top:825px;font-size:7.2px"><span class="ring" style="width:20px;height:20px"><svg width="11" height="11" viewBox="0 0 10 10"><circle cx="5" cy="5" r="4.2" fill="none" stroke="#fff"/><ellipse cx="5" cy="5" rx="1.8" ry="4.2" fill="none" stroke="#fff"/><path d="M.8 5H9.2" stroke="#fff"/></svg></span>corvantshield.com</div>
  <div class="social" style="left:346px;top:853px"><span style="width:10px;height:10px"></span><span style="width:10px;height:10px"></span></div>
</section>

</body>
</html>
```